Brimlow OrthoLink IT Inc. new website

i need a website for my company which is dedicated to installation and service of computer systems in Dental Offices. I would like for it to encompass a technology feel and professional look. The company deals with all aspects of technology like, Audio Visual, computer systems and networks, Cloud services like data backup, data center. We provide manage services, support and services to Dental Professionals.
Updates

Looking for a Technology font but professional look Added Wednesday, April 20, 2016

Target Market(s)

Dental, Dentist

Industry/Entity Type

Dental

Number of Pages Required

5+ page

Font styles to use
Other font styles liked:
• Futuristic or Techy

Colors
0255a3
ec1f27

Requirements
Must have
• Tabs
Nice to have
• Have no idea maybe some suggestion on your part may help
Should not have
• A professional feel but have a techy look

```html
<!DOCTYPE html>
<html lang="en">
<head>
<meta charset="utf-8">
<title>Brimlow OrthoLink IT Inc.</title>
<link href="https://fonts.googleapis.com/css2?family=Lato:wght@700;900&family=Open+Sans:wght@400;600;700&family=Raleway:wght@300;400;600&family=Roboto+Condensed:wght@400;700&display=swap" rel="stylesheet">
<style>
:root{
  --brand:#0255a3;
  --brand-light:#3a7cc0;
  --ink:#111;
  --body:#666;
  --white:#fff;
  --footer:#3a3a3a;
  --footer-base:#232323;
  --hero-a:#e9eef3;
  --hero-b:#c9d7e4;
}
*{margin:0;padding:0;box-sizing:border-box}
html,body{width:1200px;height:2233px;overflow:hidden;background:var(--white)}
body{position:relative;font-family:"Open Sans",sans-serif;color:var(--body)}
.abs{position:absolute}

/* Header */
.logo{left:79px;top:30px;height:68px;display:flex;align-items:center;gap:12px;font-family:"Open Sans",sans-serif;font-weight:700;font-size:40px;color:var(--brand)}
.logo-mark{width:22px;height:22px;background:var(--brand);border-radius:4px}
.contact-item{display:flex;align-items:center;gap:14px;top:27px;height:56px}
.contact-item .ring{width:56px;height:56px;border:2px solid var(--brand);border-radius:50%;display:flex;align-items:center;justify-content:center}
.phone{left:588px;font-family:"Open Sans",sans-serif;font-weight:700;font-size:25px;color:var(--brand)}
.email{left:859px;font-size:19px;color:var(--brand)}
.divider{left:840px;top:35px;width:1px;height:44px;background:#ddd}

/* Hero */
.hero{left:0;top:147px;width:1200px;height:624px;background:linear-gradient(90deg,var(--hero-b) 0%,var(--hero-a) 45%,#f4f7fa 100%)}
.nav{left:77px;top:118px;width:1046px;height:56px;background:var(--brand);display:flex;align-items:center;font-family:"Roboto Condensed",sans-serif;font-size:19px;color:var(--white)}
.nav a{color:var(--white);text-decoration:none;text-transform:uppercase;padding:0 33px;height:56px;display:flex;align-items:center}
.nav a.active{background:#000;width:122px;justify-content:center;padding:0}
.hero-text{right:95px;top:315px;text-align:right}
.hero-title{font-family:"Lato",sans-serif;font-weight:900;font-size:44px;line-height:62px;color:var(--ink)}
.hero-sub{font-family:"Roboto Condensed",sans-serif;font-size:20px;line-height:31px;color:#222;margin-top:6px}
.btn-primary{right:77px;top:526px;width:203px;height:62px;background:var(--brand);border-radius:5px;color:var(--white);font-family:"Roboto Condensed",sans-serif;font-weight:700;font-size:24px;display:flex;align-items:center;justify-content:center}

/* Section titles */
.section-title{left:0;width:1200px;text-align:center;font-family:"Raleway",sans-serif;font-weight:400;font-size:45px;color:var(--ink);text-transform:uppercase}
.section-title .accent{color:var(--brand-light)}
.intro{left:170px;width:860px;text-align:center;font-size:15px;line-height:25px;color:var(--body)}

/* Services */
.service{width:330px;text-align:center}
.service .icon{width:124px;height:124px;margin:0 auto;border:1.5px solid var(--brand);border-radius:50%;display:flex;align-items:center;justify-content:center}
.service h3{margin-top:22px;font-family:"Raleway",sans-serif;font-weight:400;font-size:23px;line-height:33px;color:var(--ink);text-transform:uppercase}
.service p{margin-top:8px;font-size:15px;line-height:25px;color:var(--body)}

/* Support band */
.support{left:0;top:1377px;width:1200px;height:312px;background:linear-gradient(90deg,#2d6eb5,#3c7cc0 50%,#2f6db0)}
.support .section-title{color:var(--white);font-weight:300;top:43px}
.support .intro{top:114px;color:var(--white)}
.btn-light{left:491px;top:194px;width:218px;height:56px;background:var(--white);border-radius:3px;font-family:"Raleway",sans-serif;font-weight:600;font-size:22px;color:var(--ink);display:flex;align-items:center;justify-content:center}

/* Testimonials */
.avatar{width:124px;height:124px;border-radius:50%;border:2px solid var(--brand);background:linear-gradient(160deg,#d9dde2,#9fa9b4)}
.quote{width:340px;font-size:15px;line-height:28px;color:var(--body)}
.quote .name{margin-top:6px;font-size:14px;font-weight:700;color:var(--brand);text-transform:uppercase}

/* Footer */
.footer{left:0;top:2009px;width:1200px;height:172px;background:var(--footer);color:var(--white)}
.footer h4{font-family:"Open Sans",sans-serif;font-weight:400;font-size:21px}
.links{display:grid;grid-template-columns:190px 190px;row-gap:8px;font-size:15px;margin-top:14px}
.socials{display:flex;gap:22px;margin-top:16px}
.socials span{width:52px;height:52px;border:2px solid var(--white);border-radius:50%}
.socials span.on{background:var(--white)}
.subscribe{display:flex;margin-top:16px;width:314px;height:41px}
.subscribe .field{flex:1;background:var(--footer);border:1px solid var(--white);font-size:15px;padding:8px 8px;color:var(--white)}
.subscribe .go{width:137px;background:var(--white);color:var(--brand);font-weight:700;font-size:15px;display:flex;align-items:center;justify-content:center}
.copyright{left:0;top:2181px;width:1200px;height:52px;background:var(--footer-base);color:var(--white);font-size:15px;display:flex;align-items:center;justify-content:center}
</style>
</head>
<body>

<!-- Header -->
<div class="abs logo">OrthoLink IT <span class="logo-mark"></span></div>
<div class="abs contact-item phone">
  <span class="ring"><svg width="26" height="26" viewBox="0 0 24 24"><path d="M6.6 10.8a15 15 0 006.6 6.6l2.2-2.2c.3-.3.7-.4 1-.2 1.1.4 2.3.6 3.6.6.6 0 1 .4 1 1V20c0 .6-.4 1-1 1A17 17 0 013 4c0-.6.4-1 1-1h3.5c.6 0 1 .4 1 1 0 1.3.2 2.5.6 3.6.1.3 0 .7-.2 1z" fill="#111"/></svg></span>
  555 201 7734
</div>
<div class="abs divider"></div>
<div class="abs contact-item email">
  <span class="ring"><svg width="26" height="20" viewBox="0 0 26 20"><rect x="1.5" y="1.5" width="23" height="17" rx="2" fill="none" stroke="#111" stroke-width="2"/><path d="M2 3l11 8 11-8" fill="none" stroke="#111" stroke-width="2"/></svg></span>
  info@ortholinkit.example
</div>

<!-- Hero -->
<div class="abs hero" role="img" aria-label="Photo of a doctor in a white coat working at a laptop in a bright clinic office"></div>
<nav class="abs nav">
  <a class="active">Home</a><a>About</a><a>Services</a><a>Support</a><a>Client</a><a>Blog</a><a>Contact</a>
</nav>
<div class="abs hero-text">
  <div class="hero-title">TECHNOLOGY FOR<br>BEST PRACTICE</div>
  <div class="hero-sub">f you view technology as an expense rather than<br>an investment, you haven't worked with us.</div>
</div>
<div class="abs btn-primary">CONTACT US</div>

<!-- Welcome -->
<h1 class="abs section-title" style="top:815px">Welcome to <span class="accent">OrthoLink IT</span></h1>
<p class="abs intro" style="top:886px">Lorem Ipsum is simply dummy text of the printing and typesetting industry. Lorem Ipsum has been the industry's standard dummy text ever since the 1500s, when an unknown printer took a galley of type and scrambled it to make a type specimen book.</p>

<div class="abs service" style="left:72px;top:1014px">
  <div class="icon"><svg width="56" height="50" viewBox="0 0 56 50"><rect x="3" y="3" width="50" height="32" rx="2" fill="none" stroke="#0255a3" stroke-width="4"/><rect x="17" y="11" width="22" height="16" fill="#0255a3"/><rect x="24" y="36" width="8" height="8" fill="#111"/><rect x="16" y="44" width="24" height="4" fill="#111"/></svg></div>
  <h3>Audio Visual</h3>
  <p>Lorem Ipsum is simply dummy text of the printing and typesetting industry. Lorem Ipsum has been the industry.</p>
</div>
<div class="abs service" style="left:435px;top:1014px">
  <div class="icon"><svg width="70" height="56" viewBox="0 0 70 56"><rect x="2" y="14" width="28" height="18" rx="2" fill="none" stroke="#0255a3" stroke-width="4"/><rect x="2" y="36" width="28" height="6" fill="#0255a3"/><path d="M34 26h8M42 6v44M42 6h10M42 22h10M42 36h10M42 50h10" stroke="#0255a3" stroke-width="3" fill="none"/><g fill="none" stroke="#0255a3" stroke-width="3"><rect x="53" y="1" width="11" height="10" rx="2"/><rect x="53" y="17" width="11" height="10" rx="2"/><rect x="53" y="31" width="11" height="10" rx="2"/><rect x="53" y="45" width="11" height="10" rx="2"/></g></svg></div>
  <h3>Computer Systems and Networks</h3>
  <p>Lorem Ipsum is simply dummy text of the printing and typesetting industry. Lorem Ipsum has been the industry.</p>
</div>
<div class="abs service" style="left:801px;top:1014px">
  <div class="icon"><svg width="70" height="58" viewBox="0 0 70 58"><path d="M16 34a12 12 0 01-1-24 16 16 0 0130-4 11 11 0 0112 13" fill="none" stroke="#0255a3" stroke-width="4"/><ellipse cx="42" cy="30" rx="12" ry="5" fill="#0255a3"/><path d="M30 30v18c0 3 5 5 12 5s12-2 12-5V30" fill="#0255a3"/><path d="M30 38c0 3 5 5 12 5s12-2 12-5M30 45c0 3 5 5 12 5" stroke="#fff" stroke-width="2" fill="none"/><circle cx="56" cy="46" r="9" fill="#fff" stroke="#0255a3" stroke-width="3"/><path d="M52 46a4 4 0 108-1" stroke="#0255a3" stroke-width="2" fill="none"/></svg></div>
  <h3>Cloud Services of Data Backup</h3>
  <p>Lorem Ipsum is simply dummy text of the printing and typesetting industry. Lorem Ipsum has been the industry.</p>
</div>

<!-- Support band -->
<section class="abs support" role="img" aria-label="Blue-tinted photo of a dental treatment room">
  <h2 class="abs section-title">Support with us</h2>
  <p class="abs intro">Lorem Ipsum is simply dummy text of the printing and typesetting industry. Lorem Ipsum has been the industry's standard dummy text ever since the 1500s, when an unknown printer took a galley.</p>
  <div class="abs btn-light">GET SUPPORT</div>
</section>

<!-- Testimonials -->
<h2 class="abs section-title" style="top:1731px;font-size:38px">What our <span class="accent">client say</span></h2>
<svg class="abs" style="left:586px;top:1793px" width="30" height="26" viewBox="0 0 30 26"><path d="M0 26V14C0 6 4 1 12 0v5c-4 1-6 4-6 8h6v13zM18 26V14c0-8 4-13 12-14v5c-4 1-6 4-6 8h6v13z" fill="#888"/></svg>

<div class="abs avatar" style="left:78px;top:1818px" role="img" aria-label="Client portrait photo"></div>
<div class="abs quote" style="left:225px;top:1818px">
  Lorem Ipsum is simply dummy text of the printing and typesetting industry. Lorem Ipsum has been the industry's standard dummy text.
  <div class="name">- Client Name</div>
</div>
<div class="abs avatar" style="left:634px;top:1818px" role="img" aria-label="Client portrait photo"></div>
<div class="abs quote" style="left:781px;top:1818px">
  Lorem Ipsum is simply dummy text of the printing and typesetting industry. Lorem Ipsum has been the industry's standard dummy text.
  <div class="name">- Client Name</div>
</div>

<!-- Footer -->
<footer class="abs footer">
  <div class="abs" style="left:78px;top:29px">
    <h4>Useful Links</h4>
    <div class="links"><span>Home</span><span>Support</span><span>About</span><span>News</span><span>Services</span><span>Contact</span></div>
  </div>
  <div class="abs" style="left:446px;top:29px">
    <h4>Follow Us</h4>
    <div class="socials"><span class="on" aria-label="Social link"></span><span aria-label="Social link"></span><span aria-label="Social link"></span><span aria-label="Social link"></span></div>
  </div>
  <div class="abs" style="left:812px;top:29px">
    <h4>Newsletter</h4>
    <div style="font-size:15px;margin-top:10px">Subscribe to stay on OrthoLink IT.</div>
    <div class="subscribe"><span class="field">Enter Email</span><span class="go">SUBSCRIBE</span></div>
  </div>
</footer>
<div class="abs copyright">©&nbsp;<b>ORTHOLINK IT</b>&nbsp;- 2016. All Rights Reserved.</div>

</body>
</html>
```